Business Card Design Project

Business Card
We are rebranding with a new logo
Industry/Entity Type
Business
Contact Information for Business Card
Dennis Morvale +61 487215963 dennis@quorv.com.au P.O. Box 872 Fernlow QLD 4309
Requirements
Must have
- Logo

```html
<!DOCTYPE html>
<html lang="en">
<head>
<meta charset="utf-8">
<title>Quorv International – Business Card</title>
<link rel="stylesheet" href="https://fonts.googleapis.com/css2?family=Source+Sans+3:wght@400;600;700&display=swap">
<style>
  :root {
    --page-bg: #e4e6e8;
    --card-white: #f7f7f7;
    --brand-blue: #0a74a8;
    --band-light: #0aa3dc;
    --band-mid: #0785bb;
    --band-dark: #0a4f72;
    --accent-orange: #f08a1c;
    --text-white: #ffffff;
  }
  * { box-sizing: border-box; margin: 0; padding: 0; }
  html, body {
    width: 1200px;
    height: 915px;
    overflow: hidden;
    background: var(--page-bg);
    font-family: "Source Sans 3", "Myriad Pro", Arial, sans-serif;
  }
  .business-card {
    position: absolute;
    left: 100px;
    top: 171px;
    width: 1000px;
    height: 573px;
    background: var(--card-white);
    overflow: hidden;
  }
  .brand-area {
    position: absolute;
    left: 0;
    top: 0;
    width: 100%;
    height: 390px;
    display: flex;
    align-items: center;
    justify-content: center;
    gap: 18px;
  }
  .brand-dot {
    width: 26px;
    height: 26px;
    border-radius: 50%;
    background: var(--accent-orange);
  }
  .brand-name {
    font-size: 60px;
    font-weight: 600;
    color: var(--brand-blue);
    letter-spacing: 1px;
  }
  .contact-band {
    position: absolute;
    left: 0;
    top: 390px;
    width: 100%;
    height: 183px;
    background:
      radial-gradient(ellipse 420px 200px at 52% 45%, var(--band-light) 0%, var(--band-mid) 45%, var(--band-dark) 100%);
    color: var(--text-white);
  }
  .holder {
    position: absolute;
    left: 45px;
    top: 34px;
  }
  .holder-name {
    font-size: 27px;
    font-weight: 700;
    color: var(--accent-orange);
    text-transform: uppercase;
    margin-bottom: 8px;
  }
  .holder-address {
    font-size: 24px;
    line-height: 33px;
  }
  .contact-list {
    position: absolute;
    right: 45px;
    top: 52px;
    list-style: none;
    text-align: right;
    font-size: 23px;
    line-height: 33px;
  }
  .contact-list li {
    display: flex;
    align-items: center;
    justify-content: flex-end;
    gap: 12px;
  }
  .contact-icon {
    width: 20px;
    height: 20px;
    flex: none;
  }
</style>
</head>
<body>
  <main class="business-card">
    <section class="brand-area">
      <span class="brand-dot"></span>
      <span class="brand-name">Quorv International</span>
    </section>

    <section class="contact-band">
      <div class="holder">
        <p class="holder-name">Dennis Morvale</p>
        <p class="holder-address">P.O. Box 872<br>Fernlow QLD 4309</p>
      </div>

      <ul class="contact-list">
        <li>+61 487215963
          <svg class="contact-icon" viewBox="0 0 20 20" aria-hidden="true">
            <path d="M2 7c0-3 4-4 8-4s8 1 8 4v1h-4V6.5c-1-.5-2.5-.7-4-.7s-3 .2-4 .7V8H2z" fill="var(--accent-orange)"/>
            <path d="M5 9h10l2 8H3z" fill="var(--accent-orange)"/>
            <circle cx="10" cy="13" r="2.2" fill="var(--band-mid)"/>
          </svg>
        </li>
        <li>dennis@quorv.com.au
          <svg class="contact-icon" viewBox="0 0 20 20" aria-hidden="true">
            <rect x="2" y="5" width="16" height="11" fill="var(--accent-orange)"/>
            <path d="M2 5l8 6 8-6" fill="none" stroke="var(--band-mid)" stroke-width="1.5"/>
          </svg>
        </li>
        <li>www.quorv.com.au
          <svg class="contact-icon" viewBox="0 0 20 20" aria-hidden="true">
            <circle cx="10" cy="10" r="8" fill="var(--accent-orange)"/>
            <path d="M6 6c2 1 1 3 3 3s1 3 3 3M13 5c-1 2 1 3 2 3" fill="none" stroke="var(--band-mid)" stroke-width="1.5"/>
          </svg>
        </li>
      </ul>
    </section>
  </main>
</body>
</html>
```